Salon and Spa Distributor Business Card

Need a business card. We are are distributor in the salon and spa industry. We identify with natural beauty. Need a card with:
Company Name: Petal Quarry"
Title: "President & CEO"
Address
Company Phone number
email
website
Tag Line:" The Professional Salon Source"

Industry/Entity Type

Business

Contact Information for Business Card

Name: Dov Strommen
Title: "President & CEO"
Address: 31 Harlow Ln, Bexmoor, NJ 07813
Company Phone number: 800-463-5918
email: dovstrommen@petalquarry.example
website: www.petalquarry.example

Requirements
Should not have
• No black backgrounds

```html
<!DOCTYPE html>
<html lang="en">
<head>
<meta charset="utf-8">
<title>Petal Quarry — Business Card</title>
<link href="https://fonts.googleapis.com/css2?family=Questrial&display=swap" rel="stylesheet">
<style>
  :root {
    --backdrop: #e9e9e9;
    --green-deep: #005f2a;
    --green-mid: #0e6b2c;
    --green-soft: #2f7d3f;
    --green-bright: #3cb43c;
    --paper: #f7f7f7;
    --ink: #444444;
    --white: #ffffff;
  }
  * { margin: 0; padding: 0; box-sizing: border-box; }
  html, body {
    width: 1200px; height: 576px; overflow: hidden;
    background: var(--backdrop);
    font-family: "Questrial", "Century Gothic", sans-serif;
  }
  .stage { position: relative; width: 1200px; height: 576px; }
  .card {
    position: absolute; top: 138px;
    width: 484px; height: 294px;
    border-radius: 13px; overflow: hidden;
    box-shadow: 0 2px 6px rgba(0,0,0,0.18);
  }
  .card--front {
    left: 82px;
    background: linear-gradient(180deg, var(--green-deep) 0%, var(--green-soft) 100%);
  }
  .front-mark {
    position: absolute; left: 217px; top: 80px;
    width: 50px; height: 50px; border-radius: 50%;
    background: var(--white);
  }
  .front-name {
    position: absolute; left: 0; right: 0; top: 176px;
    text-align: center; color: var(--white);
    font-size: 30px; letter-spacing: 0.2px;
  }
  .card--back { left: 602px; background: var(--paper); }
  .back-mark {
    position: absolute; left: 62px; top: 88px;
    width: 92px; height: 92px; border-radius: 50%;
    background: var(--green-bright);
  }
  .brand-name {
    position: absolute; left: 233px; top: 66px;
    font-size: 26px; color: var(--green-mid);
  }
  .job-title {
    position: absolute; left: 234px; top: 96px;
    font-size: 10.5px; color: var(--ink);
  }
  .contact-list { position: absolute; left: 237px; top: 120px; list-style: none; }
  .contact-list li {
    display: flex; align-items: center; height: 19px;
    font-size: 12.5px; color: var(--ink);
  }
  .contact-list svg { width: 11px; height: 11px; margin-right: 8px; fill: var(--green-mid); }
  .address {
    position: absolute; left: 234px; top: 180px;
    font-size: 12.5px; color: var(--ink);
  }
  .tag-band { position: absolute; left: 0; bottom: 0; width: 484px; height: 40px; }
  .tagline {
    position: absolute; left: 233px; bottom: 13px;
    font-size: 12.5px; color: var(--white);
  }
</style>
</head>
<body>
<main class="stage">
  <section class="card card--front" aria-label="Card front">
    <div class="front-mark"></div>
    <p class="front-name">Petal Quarry</p>
  </section>

  <section class="card card--back" aria-label="Card back">
    <div class="back-mark"></div>
    <h1 class="brand-name">Petal Quarry</h1>
    <p class="job-title">President &amp; CEO</p>
    <ul class="contact-list">
      <li><svg viewBox="0 0 12 12"><path d="M1 4.5C1 3 2.5 2 6 2s5 1 5 2.5L9 5V4H3v1zM2.5 6h7L10.5 10h-9z"/></svg>800-463-5918</li>
      <li><svg viewBox="0 0 12 12"><path d="M0.5 2.5h11v7h-11z M1.2 3L6 6.5 10.8 3" stroke="#f7f7f7" stroke-width="0.8"/></svg>dovstrommen@petalquarry.example</li>
      <li><svg viewBox="0 0 12 12"><circle cx="6" cy="6" r="5.3"/><path d="M0.7 6h10.6M6 0.7v10.6M6 0.7c-3 3-3 7.6 0 10.6M6 0.7c3 3 3 7.6 0 10.6" stroke="#f7f7f7" stroke-width="0.7" fill="none"/></svg>www.petalquarry.example</li>
    </ul>
    <p class="address">31 Harlow Ln, Bexmoor, NJ 07813</p>
    <svg class="tag-band" viewBox="0 0 484 40" preserveAspectRatio="none" aria-hidden="true">
      <rect x="0" y="21" width="484" height="19" fill="var(--green-bright)"/>
      <polygon points="208,0 484,0 484,40 182,40" fill="var(--green-deep)"/>
    </svg>
    <p class="tagline">The Professional Salon Source</p>
  </section>
</main>
</body>
</html>
```